Brookvane Consulting Business Card Design

Business Card Design for Brookvane Consulting. Brookvane Consulting is a boutique consultancy based in Atlanta, GA., that specializes in marketing strategy, organization planning, and leadership development. We provide solutions for small businesses and startups as well as Vantage 300 companies.

http://brookvaneconsulting.com/

Target Market(s)

We provide solutions for small businesses and startups as well as Vantage 300 companies.

Industry/Entity Type

Consulting

Contact Information for Business Card

Two sided business card with priority on contact information, logo, tag line (Inspiration to Dream More, Do More, Become More)

Colors

Designer to choose colors to be used in the design.

Requirements
Must have
• contact information, logo, tag line (Inspiration to Dream More, Do More, Become More)
• Simple no over communication.
Nice to have
• I would like to see different placements of logo and creative use of both sides of the card
Should not have
• Do not put too much information on the card.

```html
<!DOCTYPE html>
<html lang="en">
<head>
<meta charset="utf-8">
<title>Brookvane Consulting — Business Card</title>
<link rel="stylesheet" href="https://fonts.googleapis.com/css2?family=Dancing+Script:wght@700&family=Lato:wght@400&display=swap">
<style>
  :root {
    --backdrop: #e6e3df;
    --card-dark: #333333;
    --card-light: #f3f3f3;
    --ink-light: #ffffff;
    --ink-dark: #333333;
  }
  * { margin: 0; padding: 0; box-sizing: border-box; }
  html, body {
    width: 1200px; height: 900px; overflow: hidden;
    background: var(--backdrop);
  }
  .card {
    position: absolute; left: 160px; top: 178px;
    width: 880px; height: 544px;
    background: var(--card-light);
    box-shadow: 0 10px 30px rgba(0,0,0,0.15);
    overflow: hidden;
    font-family: "Lato", sans-serif;
  }
  .card-art { position: absolute; inset: 0; width: 100%; height: 100%; }
  .contact-block {
    position: absolute; left: 39px; top: 30px;
    color: var(--ink-light);
  }
  .person-name {
    font-family: "Dancing Script", cursive;
    font-size: 34px; line-height: 1.1;
  }
  .person-title { font-size: 23px; line-height: 1.2; margin-bottom: 20px; }
  .contact-list { list-style: none; }
  .contact-list li {
    display: flex; align-items: center; gap: 9px;
    font-size: 23px; line-height: 32px;
  }
  .contact-icon { width: 18px; height: 18px; fill: var(--ink-light); flex: none; }
  .tagline {
    position: absolute; left: 39px; top: 272px;
    font-family: "Dancing Script", cursive;
    font-size: 36px; line-height: 47px;
    color: var(--ink-light);
  }
  .brand-name {
    position: absolute; left: 468px; top: 356px;
    font-family: "Lato", sans-serif; font-weight: 400;
    color: var(--ink-dark); line-height: 1;
  }
  .brand-name .brand-main { display: block; font-size: 62px; }
  .brand-name .brand-sub { display: block; font-size: 27px; letter-spacing: 3px; margin-top: 8px; padding-left: 4px; }
</style>
</head>
<body>
  <article class="card">
    <svg class="card-art" viewBox="0 0 880 544" aria-hidden="true">
      <polygon points="0,0 738,0 205,544 0,544" fill="var(--card-dark)"/>
      <line x1="205" y1="544" x2="733" y2="20" stroke="var(--ink-light)" stroke-width="3"/>
      <polygon points="748,6 728,26 735,33 721,19 728,26" fill="var(--card-dark)"/>
      <polygon points="750,4 736,34 720,18" fill="var(--card-dark)" stroke="var(--ink-light)" stroke-width="2" stroke-linejoin="round"/>
    </svg>

    <section class="contact-block">
      <h1 class="person-name">Daniel Hargrove</h1>
      <p class="person-title">Managing Director</p>
      <ul class="contact-list">
        <li>
          <svg class="contact-icon" viewBox="0 0 24 24"><path d="M3 9c0-3 4-5 9-5s9 2 9 5v2h-5V9c-1-1-7-1-8 0v2H3zM6 13h12l2 7H4z"/></svg>
          404 555 0172
        </li>
        <li>
          <svg class="contact-icon" viewBox="0 0 24 24"><path d="M2 5h20v14H2zM4 7v1l8 5 8-5V7l-8 5z"/></svg>
          hello@brookvanemail.com
        </li>
        <li>
          <svg class="contact-icon" viewBox="0 0 24 24"><circle cx="12" cy="12" r="10"/></svg>
          www.brookvaneconsulting.com
        </li>
      </ul>
    </section>

    <p class="tagline">Inspiration to<br>Dream More<br>Do More,<br>Become More</p>

    <p class="brand-name">
      <span class="brand-main">Brookvane</span>
      <span class="brand-sub">CONSULTING</span>
    </p>
  </article>
</body>
</html>
```